Local Flower Farm Needs Business Card Design

I need business cards designed for a flower farm based in Eudora, Kansas.
Business Info:
We are a local cut flower farm located in Eudora, Kansas, founded by Corinne Haldwick. What started as a passion for agriculture and search for more joy in daily life has blossomed into a small business dedicated to providing the community with beautiful, fresh, and sustainable flowers. We specialize in local, seasonal blooms, ensuring that every petal reflects the care and dedication we pour into our craft. Our mission is to deliver the highest quality flowers directly to our customers through local farmers markets and to florists who share our commitment to sustainability. Join us in celebrating the beauty of nature, one bloom at a time!
Contact Details:
Corinne Haldwick
Owner
Phone 913-555-0147
Facebook: Rosalind Thorpe Gardens
Instagram: @RosalindThorpeGardens
Website: RosalindThorpeGardens.example
Target Market(s)
Wholesale to Florists and Direct to Consumer via Farmers Market
Industry/Entity Type
Florist, Farm
Contact Information for Business Card
Name, Contact Info, Logo
Look and feel
Each slider illustrates characteristics of the customer's brand and the style your logo design should communicate.

```html
<!DOCTYPE html>
<html lang="en">
<head>
<meta charset="utf-8">
<title>Rosalind Thorpe Gardens – Business Card</title>
<link href="https://fonts.googleapis.com/css2?family=Tinos:wght@400;700&display=swap" rel="stylesheet">
<style>
  :root {
    --backdrop: #e4e9ea;
    --ink: #0b2730;
    --paper: #f0f0f0;
    --paper-emboss: #e3e3e3;
    --on-ink: #f2f2f2;
  }
  * { margin: 0; padding: 0; box-sizing: border-box; }
  html, body { width: 1200px; height: 960px; overflow: hidden; }
  body {
    background: var(--backdrop);
    font-family: "Tinos", "Times New Roman", serif;
    position: relative;
  }
  .card {
    position: absolute;
    left: 250px;
    width: 701px;
    height: 400px;
    border-radius: 22px;
    overflow: hidden;
  }
  .card-front { top: 60px; background: var(--ink); }
  .card-back { top: 500px; background: var(--paper); color: var(--ink); }

  .brand-seal {
    position: absolute;
    display: flex;
    align-items: center;
    justify-content: center;
    text-align: center;
    border-radius: 50%;
    font-weight: 400;
    text-transform: uppercase;
    letter-spacing: 0.14em;
    line-height: 1.35;
  }
  .card-front .brand-seal {
    left: 224px; top: 74px;
    width: 252px; height: 252px;
    border: 1px solid var(--on-ink);
    color: var(--on-ink);
    font-size: 21px;
  }
  .card-back .brand-seal {
    left: 27px; top: 28px;
    width: 178px; height: 178px;
    border: 1px solid var(--ink);
    color: var(--ink);
    font-size: 15px;
  }

  .holder {
    position: absolute;
    right: 51px;
    top: 26px;
    text-align: right;
  }
  .holder-name {
    font-weight: 700;
    font-size: 33px;
    letter-spacing: 0.02em;
    color: #111;
    line-height: 1.1;
  }
  .holder-role {
    font-size: 17px;
    color: #222;
    letter-spacing: 0.03em;
    margin-top: 2px;
  }
  .holder-bar {
    position: absolute;
    right: 0; top: 30px;
    width: 19px; height: 61px;
    background: var(--ink);
  }

  .emboss-name {
    position: absolute;
    right: 14px;
    top: 140px;
    text-align: right;
    font-size: 52px;
    line-height: 1.05;
    color: var(--paper-emboss);
    text-shadow: none;
  }

  .contact-list {
    position: absolute;
    left: 24px;
    top: 284px;
    list-style: none;
  }
  .contact-list li {
    display: flex;
    align-items: center;
    height: 23.7px;
    font-size: 17px;
    letter-spacing: 0.02em;
    color: #1c1c1c;
  }
  .contact-icon {
    width: 18px; height: 18px;
    margin-right: 9px;
    flex: none;
  }
  .icon-dot { border-radius: 50%; background: var(--ink); }
  .icon-square { border: 2px solid var(--ink); border-radius: 4px; }
</style>
</head>
<body>
  <section class="card card-front" aria-label="Card front">
    <div class="brand-seal">Rosalind<br>Thorpe<br>Gardens</div>
  </section>

  <section class="card card-back" aria-label="Card back">
    <div class="brand-seal">Rosalind<br>Thorpe<br>Gardens</div>

    <div class="holder">
      <div class="holder-name">Corinne Haldwick</div>
      <div class="holder-role">Owner</div>
    </div>
    <div class="holder-bar"></div>

    <div class="emboss-name">Rosalind<br>Thorpe<br>Gardens</div>

    <ul class="contact-list">
      <li>
        <svg class="contact-icon" viewBox="0 0 24 24" aria-hidden="true">
          <path fill="#0b2730" d="M6.6 10.8c1.4 2.8 3.8 5.1 6.6 6.6l2.2-2.2c.3-.3.7-.4 1-.2 1.1.4 2.3.6 3.6.6.6 0 1 .4 1 1V20c0 .6-.4 1-1 1C10.6 21 3 13.4 3 4c0-.6.4-1 1-1h3.5c.6 0 1 .4 1 1 0 1.3.2 2.5.6 3.6.1.3 0 .7-.2 1z"/>
        </svg>
        913-555-0147
      </li>
      <li><span class="contact-icon icon-dot"></span>Rosalind Thorpe Gardens</li>
      <li><span class="contact-icon icon-square"></span>@RosalindThorpeGardens</li>
      <li>
        <svg class="contact-icon" viewBox="0 0 24 24" aria-hidden="true">
          <circle cx="12" cy="12" r="9.5" fill="none" stroke="#0b2730" stroke-width="2"/>
          <ellipse cx="12" cy="12" rx="4" ry="9.5" fill="none" stroke="#0b2730" stroke-width="1.6"/>
          <line x1="2.5" y1="12" x2="21.5" y2="12" stroke="#0b2730" stroke-width="1.6"/>
        </svg>
        RosalindThorpeGardens.example
      </li>
    </ul>
  </section>
</body>
</html>
```